Small legal and financial translation company needs Squarespace website, brochure and logo

Hello,
We are Lumarin Services (www.lumarinservices-example.com), a boutique legal and financial translation company. We offer our services mainly to Spanish customers. Our primary line of business is the translation of financial statements, but we translate a wide variety legal and financial texts.
The project we are offering comprises three parts: a redo of the current website, an informational brochure for potential customer and a logo design. These three parts should provide a consistent image. We would develop content soon.
We are looking for a website that would look like a typical law firm website, nothing too fancy. Right now, it is in English, Spanish and French, although the new site need only be in English and Spanish. There must be good toggling between the English and Spanish versions. There would be no need for tie-ins to social media and it would not contain a blog. Basically, a static site. We aren't interesting in driving traffic to the site or SEO, as we will contact nearly all potential customers beforehand. The website must be built in Squarespace to enable a smooth transition. The content would be similar to the current page, we'll be working on the exact content, but a rough draft is attached.
The brochure will be some three pages and would introduce the company to potential customers, using similar images as the website and the logo to be designed.
The only specifications for the logo is, as the website and brochure, it convey a sense of security and trust.
Feel free to ask with any questions as this is the first time we have used this platform.
Thank you!
Updates

I've added a more or less final version for the text in the brochure and updated the brief. Added Wednesday, June 10, 2015

Target Market(s)

Spanish law firms, auditors, accountants, banks, investment firms

Industry/Entity Type

Finance

Logo Text

Lumarin Services

Number of Pages Required

5+ page

Font styles to use
Serif

Requirements
Must have
• The website must be built in Squarespace and have a good option to toggle between English and Spanish versions.
• Brochure must be in both English and Spanish, I'm attaching a rough draft of the information that it will probably have. This should give an idea about what to include and the spacing. I will update it to include the final information.
Nice to have
• Would be nice to have some quality finance- and legal-related images
Should not have
• Vibrant colours

```html
<!DOCTYPE html>
<html lang="en">
<head>
<meta charset="utf-8">
<title>Lumarin Services – Trifold Brochure</title>
<link href="https://fonts.googleapis.com/css2?family=EB+Garamond:ital,wght@0,400;0,600;1,400&display=swap" rel="stylesheet">
<style>
  :root {
    --ink: #0d0d0d;
    --ink-soft: #1c1c1c;
    --paper: #ffffff;
    --stage: #5c6066;
    --stage-light: #7b7f85;
    --text-dark: #1a1a1a;
    --text-light: #e9e9e9;
    --muted-light: #bdbdbd;
    --row-grey: #d6d6d6;
    --photo-light: #d9d9d9;
    --photo-mid: #8f8f8f;
    --photo-dark: #3a3a3a;
  }
  * { box-sizing: border-box; margin: 0; padding: 0; }
  html, body { width: 852px; height: 1200px; overflow: hidden; }
  body {
    background: radial-gradient(ellipse at 50% 45%, var(--stage-light), var(--stage) 75%);
    font-family: "EB Garamond", Georgia, serif;
    position: relative;
  }
  .sheet {
    position: absolute;
    left: 66px;
    width: 720px;
    height: 556px;
    display: flex;
    box-shadow: 0 6px 18px rgba(0,0,0,.35);
  }
  .sheet--outside { top: 29px; }
  .sheet--inside { top: 615px; }
  .panel {
    position: relative;
    width: 240px;
    height: 100%;
    overflow: hidden;
  }
  .panel--light { background: var(--paper); color: var(--text-dark); }
  .panel--dark { background: var(--ink); color: var(--text-light); }
  .photo { position: absolute; left: 0; width: 100%; }
  .curve { position: absolute; left: 0; width: 100%; display: block; }

  /* outside: about panel */
  .about { position: absolute; top: 168px; left: 22px; right: 22px; }
  .about h2 { font-weight: 400; font-style: italic; font-size: 15px; margin-bottom: 5px; }
  .about p { font-size: 8.5px; line-height: 1.35; font-style: italic; margin-bottom: 14px; text-align: justify; }

  /* outside: reasons panel */
  .reasons { position: absolute; top: 22px; left: 0; right: 0; text-align: center; }
  .reasons h2 { font-weight: 400; font-size: 16px; margin-bottom: 18px; }
  .reasons ul { list-style: none; }
  .reasons li { font-size: 9.5px; line-height: 1.3; margin-bottom: 17px; padding: 0 14px; }
  .reasons svg { display: block; margin: 0 auto 4px; }
  .contact {
    position: absolute; top: 352px; left: 0; right: 0;
    text-align: center; font-size: 10px; line-height: 2; color: var(--text-light);
  }
  .fold-shade { position: absolute; left: 0; right: 0; top: 318px; height: 1px; background: #2e2e2e; }

  /* cover */
  .cover-title {
    position: absolute; top: 24px; left: 0; right: 0; text-align: center;
    font-size: 20px; letter-spacing: 3px; text-transform: uppercase; font-weight: 400;
  }
  .cover-rule { position: absolute; top: 64px; left: 0; right: 0; height: 5px; background: var(--ink); }
  .tagline {
    position: absolute; top: 372px; left: 18px; right: 18px;
    font-size: 15px; line-height: 1.25; text-align: center; color: var(--text-light);
  }
  .cover-url { position: absolute; top: 480px; left: 0; right: 0; text-align: center; font-size: 11.5px; color: var(--text-light); }

  /* inside: expertise */
  .expertise { position: absolute; top: 18px; left: 18px; right: 16px; }
  .expertise h2 { font-weight: 400; font-size: 18px; margin-bottom: 12px; }
  .expertise ol { list-style: none; }
  .expertise li { display: flex; gap: 10px; margin-bottom: 14px; }
  .step-number {
    flex: 0 0 26px; height: 26px; border: 1px solid var(--text-dark); border-radius: 50%;
    display: flex; align-items: center; justify-content: center; font-size: 14px;
  }
  .expertise h3 { font-size: 9px; font-weight: 600; margin-bottom: 2px; }
  .expertise p { font-size: 8px; line-height: 1.3; text-align: justify; }

  /* inside: comparison */
  .comparison { position: absolute; top: 16px; left: 18px; right: 18px; }
  .comparison h2 { font-weight: 400; font-size: 15px; line-height: 1.15; margin-bottom: 10px; }
  .comparison p { font-size: 7.8px; line-height: 1.35; text-align: justify; margin-bottom: 10px; color: var(--muted-light); }
  .comparison ul { list-style: none; margin: 6px 0 16px; }
  .comparison li { font-size: 8px; margin-bottom: 10px; color: var(--muted-light); }
  .comparison li::before { content: "•  "; }

  /* inside: pricing */
  .pricing { position: absolute; top: 166px; left: 18px; right: 16px; }
  .pricing h2 { font-weight: 400; font-size: 18px; margin-bottom: 10px; }
  .price-table { width: 100%; border-collapse: collapse; background: var(--row-grey); font-size: 8.5px; }
  .price-table th { background: var(--ink); color: var(--paper); text-align: left; padding: 5px 8px; font-weight: 600; }
  .price-table th:last-child, .price-table td:last-child { text-align: right; }
  .price-table td { padding: 8.5px 8px; border-bottom: 1px solid #c4c4c4; }
</style>
</head>
<body>

<section class="sheet sheet--outside" aria-label="Brochure outside">
  <div class="panel panel--light">
    <div class="photo" style="top:0;height:160px;background:linear-gradient(160deg,var(--photo-light),var(--photo-mid) 55%,var(--photo-dark));" role="img" aria-label="Photograph of a team of business professionals in suits"></div>
    <svg class="curve" style="top:128px" width="240" height="36" viewBox="0 0 240 36" aria-hidden="true">
      <path d="M0 36 L0 20 Q120 -6 240 10 L240 36 Z" fill="var(--paper)"/>
    </svg>
    <div class="about">
      <h2>Who Are We?</h2>
      <p>We are a small, highly professional team of translators with backgrounds in law, finance and interpretation. Our experience in global consulting and auditing allows us to serve law firms and companies that need accurate financial and legal documents, bridging languages across markets.</p>
      <h2>What We Do?</h2>
      <p>We provide high-quality translation services in English, Spanish and French for legal and financial documents, particularly financial statements and annual reports. Our translation tools and glossaries, refined over the years, keep every term consistent. We know the difference between local, IFRS and US GAAP statements and foster long-term relationships with our clients, following strict standards to maintain that consistency over time.</p>
    </div>
  </div>

  <div class="panel panel--dark">
    <div class="reasons">
      <h2>Why Choose Us?</h2>
      <ul>
        <li>
          <svg width="16" height="16" viewBox="0 0 16 16" aria-hidden="true"><circle cx="8" cy="8" r="6.5" fill="none" stroke="#fff" stroke-width="1.3"/><text x="8" y="11.5" font-size="10" fill="#fff" text-anchor="middle" font-family="Georgia,serif">$</text></svg>
          Save money
        </li>
        <li>
          <svg width="16" height="16" viewBox="0 0 16 16" aria-hidden="true"><path d="M8 1 L10 6 L15 6.2 L11 9.4 L12.4 14.5 L8 11.6 L3.6 14.5 L5 9.4 L1 6.2 L6 6 Z" fill="#fff"/></svg>
          Quality Guaranteed
        </li>
        <li>
          <svg width="16" height="16" viewBox="0 0 16 16" aria-hidden="true"><path d="M2 3 H14 V10 H7 L4 13 V10 H2 Z" fill="none" stroke="#fff" stroke-width="1.3"/></svg>
          Native Translators Only
        </li>
        <li>
          <svg width="16" height="16" viewBox="0 0 16 16" aria-hidden="true"><circle cx="8" cy="8" r="6.5" fill="none" stroke="#fff" stroke-width="1.3"/><path d="M8 4 V8 H11" fill="none" stroke="#fff" stroke-width="1.3"/></svg>
          Consistency Over Time<br>(develop the customer's own voice in another language)
        </li>
        <li>
          <svg width="16" height="16" viewBox="0 0 16 16" aria-hidden="true"><rect x="1.5" y="2.5" width="13" height="9" fill="none" stroke="#fff" stroke-width="1.3"/><path d="M5 14 H11" stroke="#fff" stroke-width="1.3"/></svg>
          Use of Technology Helps Cut Costs
        </li>
      </ul>
    </div>
    <div class="fold-shade"></div>
    <address class="contact" style="font-style:normal">
      212 Harbor Row, Calderra, FL 30000<br>
      (555) 010-2040<br>
      info@lumarinservices-example.com<br>
      www.lumarinservices-example.com
    </address>
  </div>

  <div class="panel panel--dark">
    <div style="position:absolute;top:0;left:0;right:0;height:70px;background:var(--paper);"></div>
    <h1 class="cover-title" style="color:var(--text-dark)">Lumarin Services</h1>
    <div class="cover-rule"></div>
    <div class="photo" style="top:69px;height:270px;background:linear-gradient(150deg,#f2f2f2,var(--photo-light) 40%,var(--photo-mid) 75%,var(--photo-dark));" role="img" aria-label="Photograph of a hand signing a document beside a figurine of Lady Justice"></div>
    <svg class="curve" style="top:300px" width="240" height="42" viewBox="0 0 240 42" aria-hidden="true">
      <path d="M0 42 L0 26 Q130 4 240 30 L240 42 Z" fill="var(--ink)"/>
      <path d="M0 26 Q130 4 240 30" fill="none" stroke="var(--paper)" stroke-width="3"/>
    </svg>
    <p class="tagline">High-quality translation services in English, Spanish and French for legal and financial documents</p>
    <p class="cover-url">www.lumarinservices-example.com</p>
  </div>
</section>

<section class="sheet sheet--inside" aria-label="Brochure inside">
  <div class="panel panel--light">
    <div class="expertise">
      <h2>Areas of Expertise</h2>
      <ol>
        <li><span class="step-number">1</span><div><h3>Duis autem vel eum iriure dolor</h3><p>Lorem ipsum dolor sit amet, consectetuer adipiscing elit, sed diam nonummy nibh euismod tincidunt ut laoreet dolore magna aliquam erat volutpat. Ut wisi enim ad minim veniam, quis nostrud exerci tation ullamcorper suscipit lobortis nisl ut aliquip ex ea commodo consequat.</p></div></li>
        <li><span class="step-number">2</span><div><h3>Duis autem vel eum iriure dolor</h3><p>Lorem ipsum dolor sit amet, consectetuer adipiscing elit, sed diam nonummy nibh euismod tincidunt ut laoreet dolore magna aliquam erat volutpat. Ut wisi enim ad minim veniam, quis nostrud exerci tation ullamcorper suscipit lobortis nisl ut aliquip ex ea commodo consequat.</p></div></li>
        <li><span class="step-number">3</span><div><h3>Duis autem vel eum iriure dolor</h3><p>Lorem ipsum dolor sit amet, consectetuer adipiscing elit, sed diam nonummy nibh euismod tincidunt ut laoreet dolore magna aliquam erat volutpat. Ut wisi enim ad minim veniam, quis nostrud exerci tation ullamcorper suscipit lobortis nisl ut aliquip ex ea commodo consequat.</p></div></li>
      </ol>
    </div>
    <div class="photo" style="top:380px;height:176px;background:linear-gradient(170deg,var(--photo-light),var(--photo-mid) 60%,var(--photo-dark));" role="img" aria-label="Photograph of a judge's gavel resting on a book in front of scales"></div>
    <svg class="curve" style="top:372px" width="240" height="40" viewBox="0 0 240 40" aria-hidden="true">
      <path d="M0 0 L240 0 L240 10 Q110 40 0 26 Z" fill="var(--paper)"/>
      <path d="M0 26 Q110 40 240 10" fill="none" stroke="var(--ink)" stroke-width="3"/>
    </svg>
  </div>

  <div class="panel panel--dark">
    <div class="comparison">
      <h2>Differences between working with a translation agency and a translation provider</h2>
      <p>Lorem ipsum dolor sit amet, consectetuer adipiscing elit, sed diam nonummy nibh euismod tincidunt ut laoreet dolore magna aliquam erat volutpat. Ut wisi enim ad minim veniam, quis nostrud exerci tation ullamcorper suscipit lobortis nisl ut aliquip ex ea commodo consequat.</p>
      <ul>
        <li>Nam liber tempor cum soluta nobis</li>
        <li>Eleifend option congue nihil imperdiet doming</li>
        <li>Id quod mazim placerat facer possim assum</li>
        <li>Typi non habent claritatem insitam; est usus</li>
        <li>Legentis in iis qui facit eorum claritatem</li>
        <li>Investigationes demonstraverunt lectores</li>
        <li>Legere me lius quod ii legunt saepius</li>
      </ul>
      <p>Duis autem vel eum iriure dolor in hendrerit in vulputate velit esse molestie consequat, vel illum dolore eu feugiat nulla facilisis at vero eros et accumsan et iusto odio dignissim qui blandit praesent luptatum zzril delenit augue duis dolore te feugait nulla facilisi. Nam liber tempor cum soluta nobis eleifend option congue nihil imperdiet doming id quod mazim placerat facer possim assum.</p>
      <p>Typi non habent claritatem insitam; est usus legentis in iis qui facit eorum claritatem. Investigationes demonstraverunt lectores legere me lius quod ii legunt saepius. Claritas est etiam processus dynamicus, qui sequitur mutationem consuetudium lectorum. Mirum est notare quam littera gothica, quam nunc putamus parum claram, anteposuerit litterarum formas humanitatis per seacula quarta decima et quinta decima.</p>
    </div>
  </div>

  <div class="panel panel--light">
    <div class="photo" style="top:0;height:150px;background:linear-gradient(160deg,#f4f4f4,var(--photo-light) 50%,var(--photo-mid));" role="img" aria-label="Photograph of a hand writing with a pen on paperwork"></div>
    <svg class="curve" style="top:112px" width="240" height="42" viewBox="0 0 240 42" aria-hidden="true">
      <path d="M0 42 L0 34 Q120 2 240 12 L240 42 Z" fill="var(--paper)"/>
      <path d="M0 34 Q120 2 240 12" fill="none" stroke="var(--ink)" stroke-width="3"/>
    </svg>
    <div class="pricing">
      <h2>Pricing</h2>
      <table class="price-table">
        <thead><tr><th>Description</th><th>Amount</th></tr></thead>
        <tbody>
          <tr><td>Lorem ipsum dolor sit amet</td><td>$100</td></tr>
          <tr><td>Consectetuer adipiscing elit</td><td>$100</td></tr>
          <tr><td>Sed diam nonummy nibh</td><td>$100</td></tr>
          <tr><td>Euismod tincidunt ut laoreet dolore</td><td>$100</td></tr>
          <tr><td>Magna aliquam erat volutpat</td><td>$100</td></tr>
          <tr><td>Ut wisi enim ad minim veniam</td><td>$100</td></tr>
          <tr><td>Quis nostrud exerci tation</td><td>$100</td></tr>
          <tr><td>Ullamcorper suscipit lobortis</td><td>$100</td></tr>
          <tr><td>Nisl ut aliquip ex ea</td><td>$100</td></tr>
          <tr><td>Commodo consequat.</td><td>$100</td></tr>
        </tbody>
      </table>
    </div>
  </div>
</section>

</body>
</html>
```